PSD Website Design

I am looking to have a custom website designed. I would like a PSD made of the design I came up with. Once I get the design I will slice the PSD and create a wordpress template from it.

See attachment for basic layout of the graphic. The image labeled Player page is the basic page I will need for the website. I also need a home page with an image slider on it and thumbnails of recent, state video uploads.

A textured background is ok.

Looking for a quick turnaround.

Text at top of page is a menu that is needed. Open to seeing the menu as a navigational bar or/and with different font types.

No preference on page background color or font colors. I welcome creativity.

```html
<!DOCTYPE html>
<html lang="en">
<head>
<meta charset="utf-8">
<title>Summit Athletic Recruiting – Player Profile</title>
<link rel="stylesheet" href="https://fonts.googleapis.com/css2?family=Bebas+Neue&family=Cabin:wght@400;600&family=Noto+Serif&family=Arimo:wght@400;700&display=swap">
<style>
:root{
  --orange:#f07d00;
  --page:#e3e4e7;
  --white:#ffffff;
  --ink:#2b2b2b;
  --blue:#2d5ea3;
  --link:#2a7bd0;
  --green:#6fa33a;
  --dark:#242424;
  --footer:#3a3a3a;
  --footer-deep:#0d0d0d;
  --sky:#7ed3f2;
  --red:#c4302b;
  --field:#8a8a8a;
}
*{box-sizing:border-box;margin:0;padding:0}
html,body{width:1176px;height:1200px;overflow:hidden}
body{position:relative;background:var(--page);font-family:"Arimo",Arial,sans-serif;color:var(--ink)}

/* header */
.site-header{position:absolute;left:0;top:0;width:1176px;height:97px;background:var(--white);border-bottom:8px solid var(--orange)}
.brand{position:absolute;left:112px;top:18px;display:flex;align-items:center;gap:8px}
.brand-dot{width:30px;height:30px;border-radius:50%;background:var(--orange)}
.brand-name{font-family:"Bebas Neue",sans-serif;font-size:34px;line-height:1;color:#111;letter-spacing:1px}
.brand-sub{position:absolute;left:112px;top:60px;font-family:"Bebas Neue",sans-serif;font-size:15px;letter-spacing:2.4px;color:#111}
.main-nav{position:absolute;top:40px;left:445px;font-family:"Cabin",sans-serif;font-size:20px;color:#6b6b6b}
.main-nav a{color:inherit;text-decoration:none;position:absolute;white-space:nowrap}
.main-nav .active{color:var(--orange)}
.nav-caret{position:absolute;left:753px;top:81px;width:0;height:0;border:8px solid transparent;border-bottom-color:var(--orange)}
.search{position:absolute;left:911px;top:39px;width:143px;height:30px;border:1px solid #bfbfbf;border-radius:3px;background:#e6e6e6;font-family:"Cabin",sans-serif;font-style:italic;font-size:14px;color:#9a9a9a;padding:6px 11px}
.search-btn{position:absolute;right:0;top:0;width:32px;height:28px;background:#d2d2d2;border-left:1px solid #bcbcbc}

/* content panel */
.panel{position:absolute;left:103px;top:110px;width:959px;height:800px;background:var(--white)}
.photo-card{position:absolute;left:120px;top:126px;width:232px;height:302px;background:var(--white);box-shadow:0 2px 8px rgba(0,0,0,.35);transform:rotate(-2deg)}
.photo-back{position:absolute;left:128px;top:130px;width:232px;height:302px;background:#f4f4f4;box-shadow:0 2px 6px rgba(0,0,0,.25);transform:rotate(1deg)}
.photo{position:absolute;left:10px;top:12px;width:212px;height:278px;background:linear-gradient(160deg,#d8e9b4,#bcd98f)}
.player-name{position:absolute;left:388px;top:126px;font-size:25px;font-weight:700;color:#222}
.player-pos{position:absolute;left:388px;top:161px;font-size:14px;font-weight:700;color:var(--blue)}
.stats{position:absolute;left:388px;top:181px;font-size:13px;color:#444;line-height:20.5px}
.stats .serif{font-family:"Noto Serif",serif;font-size:12.5px;color:#222}
.class-of{position:absolute;left:384px;top:381px;font-size:14px;font-weight:700;color:var(--green)}

.section-title{position:absolute;font-family:"Bebas Neue",sans-serif;color:var(--orange);font-size:29px;line-height:1;white-space:nowrap}
.rule{position:absolute;height:2px;background:var(--orange)}
.video{position:absolute;left:605px;top:160px;width:434px;height:266px;background:linear-gradient(180deg,#c9c9c9 0%,#7a6e6a 40%,#3a2c30 100%);border:1px solid #ccc}
.video-bar{position:absolute;left:605px;top:409px;width:434px;height:17px;background:#1c1c1c;color:#aaa;font-size:8px;padding:4px 0 0 66px}

/* game film */
.film-line{position:absolute;left:116px;top:501px;width:545px;height:5px;background:#5a5a5a}
.film-ribbon{position:absolute;left:265px;top:470px;width:216px;height:72px}
.film-label{position:absolute;left:265px;top:487px;width:216px;text-align:center;font-family:"Bebas Neue",sans-serif;font-size:29px;color:var(--white)}
.thumbs{position:absolute;left:120px;width:545px;display:flex;gap:6px}
.thumb{width:131px}
.thumb-img{position:relative;height:74px}
.dur{position:absolute;right:2px;bottom:2px;background:rgba(0,0,0,.8);color:#fff;font-size:8px;font-weight:700;padding:1px 3px}
.thumb-title{font-size:9.5px;color:var(--link);line-height:11.5px;margin-top:5px;height:24px;overflow:hidden}
.thumb-meta{font-size:7.5px;color:#777;line-height:10px}
.divider{position:absolute;left:120px;width:541px;height:1px;background:#e3e3e3}
.channel{position:absolute;left:120px;top:720px;width:541px;font-size:11px;font-weight:700;color:#333;display:flex;align-items:center;gap:6px}
.channel small{font-weight:400;font-size:8px;color:#999}
.channel-dot{width:14px;height:14px;border-radius:50%;background:#222}
.subscribe{position:absolute;left:609px;top:719px;width:52px;height:16px;background:#d9251d;color:#fff;font-size:8px;padding:3px 0 0 20px}

/* viral box */
.viral-box{position:absolute;left:696px;top:527px;width:347px;height:324px;background:var(--dark);border-radius:3px}
.event-tag{position:absolute;left:713px;top:549px;width:120px;height:34px;background:var(--white);font-family:"Bebas Neue",sans-serif;font-size:28px;color:#111;padding:3px 0 0 5px}
.event-text{position:absolute;left:713px;top:583px;width:311px;height:96px;background:var(--white);font-family:"Cabin",sans-serif;font-size:15px;line-height:20.5px;color:#111;padding:3px 4px 0 8px}
.connect{position:absolute;left:676px;top:697px;width:350px;height:38px;background:var(--sky);font-family:"Bebas Neue",sans-serif;font-size:27px;color:var(--white);padding:5px 0 0 42px}
.connect-fold{position:absolute;left:676px;top:735px;width:0;height:0;border-top:18px solid #4aa7c9;border-left:20px solid transparent}
.social{position:absolute;top:760px;width:63px;height:63px;border-radius:6px;background:linear-gradient(#fafafa,#d6d6d6);border-bottom:5px solid #2aa9d8;display:flex;align-items:center;justify-content:center;font-family:"Cabin",sans-serif;font-size:12px;font-weight:600;color:#444}

/* footer */
.site-footer{position:absolute;left:0;top:908px;width:1176px;height:254px;background:var(--footer);border-top:4px solid var(--orange)}
.foot-title{position:absolute;font-family:"Bebas Neue",sans-serif;font-size:28px;color:var(--orange)}
.foot-rule{position:absolute;left:112px;top:976px;width:190px;height:1px;background:linear-gradient(90deg,transparent,#1e1e1e 20%,#1e1e1e 80%,transparent)}
.foot-rule.two{left:380px;width:225px}
.foot-links{position:absolute;left:138px;top:986px;font-family:"Cabin",sans-serif;font-size:18px;line-height:30.5px;color:#f1f1f1;list-style:none}
.contact{position:absolute;left:380px;font-family:"Cabin",sans-serif;font-size:18px;line-height:21px;color:#f1f1f1;display:flex;gap:12px;white-space:nowrap}
.contact svg{flex:none;margin-top:2px}
.field{position:absolute;background:var(--field);border:2px solid #a9a9a9;font-family:"Cabin",sans-serif;font-style:italic;font-size:16px;color:#e8e8e8;padding:5px 8px}
.send{position:absolute;left:963px;top:1110px;width:83px;height:29px;background:var(--orange);color:var(--white);font-family:"Cabin",sans-serif;font-size:18px;text-align:center;padding-top:2px}
.copyright{position:absolute;left:0;top:1162px;width:1176px;height:38px;background:var(--footer-deep);color:#f1f1f1;font-family:"Cabin",sans-serif;font-size:16px;padding:10px 0 0 115px}
</style>
</head>
<body>

<header class="site-header">
  <div class="brand"><span class="brand-dot"></span><span class="brand-name">SUMMIT</span></div>
  <div class="brand-sub">ATHLETIC RECRUITING</div>
  <nav class="main-nav">
    <a style="left:0">Home</a>
    <a style="left:95px">About us</a>
    <a style="left:209px">State</a>
    <a style="left:285px" class="active">Position</a>
    <a style="left:393px">Join</a>
  </nav>
  <div class="search">search here...<span class="search-btn">
    <svg width="32" height="28" viewBox="0 0 32 28"><circle cx="14" cy="12" r="6" fill="none" stroke="#666" stroke-width="2.5"/><line x1="18" y1="16" x2="24" y2="22" stroke="#666" stroke-width="3"/></svg>
  </span></div>
</header>
<div class="nav-caret"></div>

<main class="panel"></main>

<div class="photo-back"></div>
<div class="photo-card"><div class="photo" role="img" aria-label="Portrait of the player in a yellow sleeveless shirt"></div></div>

<h1 class="player-name">Marcus Holloway</h1>
<div class="player-pos">Wide Receiver</div>
<div class="stats">
  Miami, FL (Lakeside Central)<br>
  Ht: 6-1.5 &nbsp;|&nbsp; Wt: 197<br>
  <span class="serif">40 Time: 4.45</span><br>
  <span class="serif">Bench:&nbsp; 22 Reps</span><br>
  <span class="serif">Vertical: 36</span><br>
  <span class="serif">5-10-5 Shuttle: 4.42</span>
</div>
<div class="class-of">CLASS OF 2015</div>

<div class="rule" style="left:604px;top:138px;width:26px"></div>
<div class="section-title" style="left:637px;top:125px">HIGHLIGHTS</div>
<div class="rule" style="left:752px;top:138px;width:300px;background:linear-gradient(90deg,var(--orange),#fbe2c4)"></div>
<div class="video" role="img" aria-label="Highlight video still of players gathered on an indoor field"></div>
<div class="video-bar">0:12 / 7:50</div>

<div class="film-line"></div>
<svg class="film-ribbon" viewBox="0 0 216 72" aria-hidden="true">
  <path d="M0 32 L24 4 L192 4 L216 32 Z" fill="#d8d8d8"/>
  <path d="M22 8 L194 8 L170 60 Q108 78 46 60 Z" fill="var(--red)"/>
  <path d="M22 8 L194 8 L188 20 L28 20 Z" fill="#e25550"/>
</svg>
<div class="film-label">GAME FILM</div>

<div class="thumbs" style="top:570px">
  <div class="thumb"><div class="thumb-img" role="img" aria-label="Model train on garden track" style="background:linear-gradient(#6f8f4a,#8b7a5a)"><span class="dur">9:56</span></div><div class="thumb-title">Valley Rail parade and other heritage vehicles</div><div class="thumb-meta">by railfan &nbsp;10,820 views<br>3 years ago</div></div>
  <div class="thumb"><div class="thumb-img" role="img" aria-label="Model railway station in a garden" style="background:linear-gradient(#9aa383,#6d6b55)"><span class="dur">7:54</span></div><div class="thumb-title">Valley Rail 5 couplers</div><div class="thumb-meta">by trainclub &nbsp;10,358 views<br>3 years ago</div></div>
  <div class="thumb"><div class="thumb-img" role="img" aria-label="Steam trains on parallel tracks" style="background:linear-gradient(#9aa3a8,#5e5c52)"><span class="dur">6:23</span></div><div class="thumb-title">Valley Rail photo special with double steam run</div><div class="thumb-meta">by steamyard &nbsp;32,118 views<br>4 years ago</div></div>
  <div class="thumb"><div class="thumb-img" role="img" aria-label="Garden railway with flowers" style="background:linear-gradient(#7fa05a,#5b6e3c)"><span class="dur">6:30</span></div><div class="thumb-title">Valley Rail in autumn 2011 part 2</div><div class="thumb-meta">by railfan &nbsp;11,410 views<br>2 years ago</div></div>
</div>
<div class="divider" style="top:712px"></div>
<div class="channel"><span class="channel-dot"></span>trackside <small>Popular channel on VideoHub - we think you'll like it.</small></div>
<div class="subscribe">Subscr</div>
<div class="thumbs" style="top:742px">
  <div class="thumb"><div class="thumb-img" role="img" aria-label="Toy engines on a blue background" style="background:linear-gradient(#2fb5e8,#c23a3a)"><span class="dur">23:45</span></div><div class="thumb-title">Little Blue Engine ultimate track build</div><div class="thumb-meta">by trackside &nbsp;17,498,131 views<br>1 year ago</div></div>
  <div class="thumb"><div class="thumb-img" role="img" aria-label="Spider toy in a red circle" style="background:linear-gradient(#c9a585,#6b3a2a)"><span class="dur">4:47</span></div><div class="thumb-title">Big spider meets the vacuum cleaner</div><div class="thumb-meta">by trackside &nbsp;4,842,690 views<br>2 years ago</div></div>
  <div class="thumb"><div class="thumb-img" role="img" aria-label="Toy engines on a wooden track" style="background:linear-gradient(#3a8ad0,#5aa84a)"><span class="dur">13:33</span></div><div class="thumb-title">Little Blue Engine and friends mash up set</div><div class="thumb-meta">by trackside &nbsp;10,769,905 views<br>2 years ago</div></div>
  <div class="thumb"><div class="thumb-img" role="img" aria-label="Toy engine with a yellow prop" style="background:linear-gradient(#d7c95a,#2a5ab0)"><span class="dur">13:17</span></div><div class="thumb-title">Little Blue Engine pirate cove play set</div><div class="thumb-meta">by trackside &nbsp;9,619,796 views<br>1 year ago</div></div>
</div>
<div class="divider" style="top:878px"></div>

<div class="rule" style="left:686px;top:505px;width:26px"></div>
<div class="section-title" style="left:715px;top:493px">TAKE IT VIRAL</div>
<div class="rule" style="left:840px;top:505px;width:222px;background:linear-gradient(90deg,var(--orange),#fbe2c4)"></div>
<div class="viral-box"></div>
<div class="event-tag">NEXT EVENT</div>
<div class="event-text">Lorem ipsum dolor sit amet,consectetuer adipiscing elit, sed diam nonummy nibh euismod tincidunt ut laoreet dolore magna aliquam erat volutpat.</div>
<div class="connect">CONNECT WITH HUDDLE</div>
<div class="connect-fold"></div>
<div class="social" style="left:716px">Share</div>
<div class="social" style="left:797px">Post</div>
<div class="social" style="left:878px">Watch</div>
<div class="social" style="left:957px">Photo</div>

<footer class="site-footer"></footer>
<div class="foot-title" style="left:140px;top:941px">QUICK LINKS</div>
<div class="foot-rule"></div>
<ul class="foot-links"><li>About us</li><li>Position</li><li>State</li><li>Join</li></ul>

<div class="foot-title" style="left:404px;top:941px">CONTACT US</div>
<div class="foot-rule two"></div>
<div class="contact" style="top:986px">
  <svg width="18" height="22" viewBox="0 0 18 22"><path d="M9 1a7 7 0 0 0-7 7c0 5 7 13 7 13s7-8 7-13a7 7 0 0 0-7-7z" fill="#8c8c8c"/><circle cx="9" cy="8" r="2.6" fill="var(--footer)"/></svg>
  <span>Address: 418 Ridge Road,<br>Brookfield, ST 40217</span>
</div>
<div class="contact" style="top:1043px">
  <svg width="18" height="20" viewBox="0 0 18 20"><path d="M4 1l3 4-2 3c1 3 3 5 6 6l2-2 4 3-2 3C8 18 1 11 1 3z" fill="#8c8c8c"/></svg>
  <span>555-0142-7720</span>
</div>
<div class="contact" style="top:1082px">
  <svg width="20" height="16" viewBox="0 0 20 16"><rect x="1" y="2" width="18" height="12" fill="none" stroke="#8c8c8c" stroke-width="1.5"/><path d="M1 2l9 7 9-7M1 14l7-6M19 14l-7-6" fill="none" stroke="#8c8c8c" stroke-width="1.5"/></svg>
  <span>hello@summitrecruit.com</span>
</div>

<div class="foot-title" style="left:750px;top:941px">GET IN TOUCH</div>
<div class="field" style="left:751px;top:983px;width:130px;height:30px">Name</div>
<div class="field" style="left:897px;top:983px;width:151px;height:30px">Email</div>
<div class="field" style="left:751px;top:1022px;width:296px;height:80px">Your Message...</div>
<div class="send">Send</div>

<div class="copyright">© 2014 Summit Athletic Recruiting, All Rights Reserved</div>
</body>
</html>
```